Stylish new business card needed!

Hello everyone! I am in need of a new business card design for an alarm company here in Hurricane WV. I have all fonts, color codes and logos provided for you use! We are a young company and like the style of a clean sleek looking business card. Would like it double sided, one side holding the logo and the other with your design!
Target Market(s)
The people that are looking for the newest tech for home automation and security
Industry/Entity Type
Alarm services; Home automation
Contact Information for Business Card
Name of person; position (Sales; Installer); Phone Number (555.418.7260); Employee cell Number; Website (www.GuardedByVelk.example); Employee Email; Double sided
Look and feel
Each slider illustrates characteristics of the customer's brand and the style your logo design should communicate.

```html
<!DOCTYPE html>
<html lang="en">
<head>
<meta charset="utf-8">
<title>Velk Business Card</title>
<link rel="stylesheet" href="https://fonts.googleapis.com/css2?family=Montserrat:wght@400;500;700&display=swap">
<style>
  :root {
    --backdrop: #d2d2d2;
    --card: #9b9b9b;
    --white: #ffffff;
    --orange: #f28c4a;
  }
  * { margin: 0; padding: 0; box-sizing: border-box; }
  html, body {
    width: 1200px; height: 788px; overflow: hidden;
    background: var(--backdrop);
    font-family: "Montserrat", Arial, sans-serif;
  }
  .sheet {
    width: 1200px; height: 788px;
    display: flex; align-items: center; justify-content: center; gap: 40px;
  }
  .card {
    position: relative;
    width: 540px; height: 309px;
    background: var(--card);
    border-radius: 22px;
    color: var(--white);
  }
  .wordmark {
    display: flex; align-items: center; gap: 10px;
    font-weight: 500; letter-spacing: 4px; color: var(--white);
  }
  .wordmark .dot {
    border-radius: 50%; background: var(--orange);
  }
  .card--front .wordmark { position: absolute; left: 58px; top: 54px; font-size: 58px; }
  .card--front .wordmark .dot { width: 16px; height: 16px; }
  .identity { position: absolute; left: 58px; top: 150px; }
  .identity__name {
    color: var(--orange); font-weight: 700; font-size: 19px; letter-spacing: 1.5px;
    text-transform: uppercase;
  }
  .identity__role { font-size: 13px; margin-top: 4px; }
  .divider {
    position: absolute; left: 268px; top: 128px; width: 1px; height: 76px;
    background: var(--orange);
  }
  .contacts { position: absolute; left: 288px; top: 130px; list-style: none; }
  .contacts li {
    display: flex; align-items: center; gap: 8px;
    font-size: 11.5px; line-height: 24px;
  }
  .contacts svg { width: 12px; height: 12px; flex: none; }
  .address {
    position: absolute; left: 58px; right: 40px; bottom: 40px;
    font-size: 12.5px; letter-spacing: 0.3px;
  }
  .card--back { display: flex; align-items: center; justify-content: center; }
  .card--back .wordmark { font-size: 96px; gap: 16px; }
  .card--back .wordmark .dot { width: 24px; height: 24px; }
</style>
</head>
<body>
<main class="sheet">
  <section class="card card--front" aria-label="Card front">
    <div class="wordmark">VELK<span class="dot"></span></div>
    <div class="identity">
      <p class="identity__name">Dana Whitfield</p>
      <p class="identity__role">Sales/Installer</p>
    </div>
    <div class="divider"></div>
    <ul class="contacts">
      <li>
        <svg viewBox="0 0 12 12" aria-hidden="true"><path fill="var(--orange)" d="M2.3 1h2l1 2.6-1.3.9a6 6 0 0 0 3.5 3.5l.9-1.3 2.6 1v2c0 .7-.6 1.3-1.3 1.3A9.7 9.7 0 0 1 1 2.3C1 1.6 1.6 1 2.3 1z"/></svg>
        555.418.7260
      </li>
      <li>
        <svg viewBox="0 0 12 12" aria-hidden="true"><rect x="0.5" y="2" width="11" height="8" rx="1" fill="var(--orange)"/><path d="M1 2.6 6 6.6l5-4" stroke="var(--card)" stroke-width="1" fill="none"/></svg>
        info@GuardedByVelk.example
      </li>
      <li>
        <svg viewBox="0 0 12 12" aria-hidden="true"><g fill="none" stroke="var(--orange)" stroke-width="1.1"><circle cx="6" cy="6" r="5"/><ellipse cx="6" cy="6" rx="2.2" ry="5"/><path d="M1 6h10"/></g></svg>
        www.GuardedByVelk.example
      </li>
    </ul>
    <p class="address">1450 W Harbor Avenue Marlow County 4180</p>
  </section>

  <section class="card card--back" aria-label="Card back">
    <div class="wordmark">VELK<span class="dot"></span></div>
  </section>
</main>
</body>
</html>
```